Allied Health team of Physiotherapists & Occupational Therapists seek a business card design

We have our new logo, we now need our new business cards and stationary. Tidewell: Oedema & Family Clinic is seeking a generic card design to represent our whole team and individual cards for each therapist that incorporates our new logo to communicate our holistic approach that is calming, nuturing, supportive and welcoming.
Our Physiotherapists and Occupational Therapists assess, treat and provide education for people who are at risk of or who have lymphoedema. This is often as a result of treatment for cancer. We provide pre-operative and post-operative management and cancer rehabilitation in our Pilates studio. Our team also consists of Physiotherapists who have a strong interest in pelvic floor and continence management for both men and women.

Target Market(s)

Mainly women health conscious

Industry/Entity Type

Allied Health: Physiotherapy / Occupational Therapy

Contact Information for Business Card

Address: 14 Gallivant Ave Marrowvale 3188 Phone: 84316570 fax: 8431 6578 Email: info@tidewellcareservices.com.au Website: tidewellcareservices.com.au Facebook address: facebook.com/TidewellOedemaAndFamilyCareClinic. Room to write appointments. Individual cards need to have name, office email and individual email and professional details

Requirements
Must have
• Logo as per uploaded documents

```html
<!DOCTYPE html>
<html lang="en">
<head>
<meta charset="utf-8">
<title>Tidewell business cards</title>
<link href="https://fonts.googleapis.com/css2?family=Lato:ital,wght@0,400;1,300&family=Sanchez&display=swap" rel="stylesheet">
<style>
  :root {
    --backdrop: #2b2b2b;
    --cream: #fefad8;
    --white: #ffffff;
    --peach: #f6a77c;
    --sage: #b9c6bd;
    --ink: #3d3d3d;
    --muted: #555555;
  }
  * { margin: 0; padding: 0; box-sizing: border-box; }
  html, body { width: 1200px; height: 936px; overflow: hidden; background: var(--backdrop); }
  body { position: relative; font-family: "Lato", sans-serif; color: var(--ink); }

  .card {
    position: absolute; width: 490px; height: 280px;
    background: var(--cream);
    box-shadow: 0 6px 18px rgba(0,0,0,.55);
  }
  .card--marla { left: 95px; top: 173px; }
  .card--appointment { left: 615px; top: 173px; background: var(--white); }
  .card--corinne { left: 95px; top: 484px; }
  .card--tessa { left: 615px; top: 484px; }

  .bar { position: absolute; left: 0; width: 7px; }
  .bar--accent { background: var(--peach); }
  .bar--contact { background: var(--sage); }

  .profile { position: absolute; left: 20px; }
  .profile__name {
    font-family: "Sanchez", serif; color: var(--peach);
    font-size: 18px; line-height: 22px; letter-spacing: .3px; font-weight: 400;
  }
  .profile__quals { font-style: italic; font-weight: 300; font-size: 9px; line-height: 12.4px; color: var(--muted); }
  .profile__role { font-size: 11.5px; line-height: 13.2px; color: var(--ink); }

  .contacts { position: absolute; left: 20px; list-style: none; }
  .contacts li { display: flex; align-items: center; font-size: 11.5px; line-height: 14.1px; white-space: nowrap; }
  .contacts svg { width: 9px; height: 9px; margin-right: 7px; flex: none; fill: var(--peach); }

  .brand {
    position: absolute; width: 168px; height: 168px; border-radius: 50%;
    border: 2px solid var(--peach); opacity: .9;
    display: flex; align-items: center; justify-content: center;
  }
  .brand__name { font-family: "Lato", sans-serif; font-size: 30px; color: var(--peach); }

  .appointment { position: absolute; inset: 0; }
  .appointment__title {
    position: absolute; top: 86px; width: 100%; text-align: center;
    font-family: "Sanchez", serif; color: var(--peach); font-size: 19px; font-weight: 400;
  }
  .field { position: absolute; font-size: 11.5px; color: var(--ink); display: flex; align-items: flex-end; }
  .field__line { display: inline-block; border-bottom: 1px solid var(--ink); height: 10px; margin-left: 3px; }
  .booking { position: absolute; left: 129px; top: 228px; display: flex; align-items: center; font-size: 11.5px; }
  .booking__link {
    margin-left: 5px; background: var(--peach); color: var(--white);
    border-radius: 8px; padding: 1px 7px; font-size: 11px;
  }
</style>
</head>
<body>

<svg width="0" height="0" style="position:absolute">
  <defs>
    <symbol id="i-pin" viewBox="0 0 10 10"><path d="M5 0a3.6 3.6 0 0 0-3.6 3.6C1.4 6.4 5 10 5 10s3.6-3.6 3.6-6.4A3.6 3.6 0 0 0 5 0zm0 5a1.4 1.4 0 1 1 0-2.8A1.4 1.4 0 0 1 5 5z"/></symbol>
    <symbol id="i-phone" viewBox="0 0 10 10"><path d="M2 .5l1.6 1.9-.9 1.3c.6 1.3 1.6 2.3 2.9 2.9l1.3-.9L9 7.3 8 9.2C4.2 9 .9 5.8.8 2z"/></symbol>
    <symbol id="i-fax" viewBox="0 0 10 10"><path d="M2.5 0h5v3h-5zM0 3.5h10v4H8V6H2v1.5H0zM2.5 6.5h5V10h-5z"/></symbol>
    <symbol id="i-mail" viewBox="0 0 10 10"><path d="M0 2h10v6H0zm1 1v.3l4 2.4 4-2.4V3z"/></symbol>
    <symbol id="i-web" viewBox="0 0 10 10"><circle cx="5" cy="5" r="4.3" fill="none" stroke="currentColor"/><path d="M.7 5h8.6M5 .7c2 2.5 2 6.1 0 8.6M5 .7c-2 2.5-2 6.1 0 8.6" fill="none" stroke="currentColor" stroke-width=".8"/></symbol>
    <symbol id="i-social" viewBox="0 0 10 10"><circle cx="5" cy="5" r="5"/></symbol>
  </defs>
</svg>

<!-- Card: Marla Penhurst -->
<section class="card card--marla">
  <div class="bar bar--accent" style="top:39px;height:93px"></div>
  <div class="bar bar--contact" style="top:150px;height:94px"></div>
  <div class="profile" style="top:34px">
    <h2 class="profile__name">Marla Penhurst</h2>
    <p class="profile__quals">B. Physio (Hons), B.App.Sci.(Human Movement/Psych)</p>
    <p class="profile__quals">Post Grad Certif. Exercise for Women</p>
    <p class="profile__quals">Post Grad Certif. Continence &amp; Pelvic Floor Rehabilitation</p>
    <p class="profile__role">Physiotherapist</p>
    <p class="profile__role">Lymphoedema &amp; Oncology Rehabilitation</p>
    <p class="profile__role">Continence &amp; Pelvic Floor</p>
  </div>
  <ul class="contacts" style="top:146px">
    <li><svg><use href="#i-pin"/></svg>14 Gallivant Ave, Marrowvale 3188</li>
    <li><svg><use href="#i-phone"/></svg>84316570 Phone</li>
    <li><svg><use href="#i-fax"/></svg>8431 6578 Fax</li>
    <li><svg><use href="#i-mail"/></svg>marla@tidewellcareservices.com.au</li>
    <li><svg><use href="#i-mail"/></svg>info@tidewellcareservices.com.au (office)</li>
    <li><svg style="color:var(--peach)"><use href="#i-web"/></svg>tidewellcareservices.com.au</li>
    <li><svg><use href="#i-social"/></svg>/TidewellOedemaAndFamilyCareClinic</li>
  </ul>
  <div class="brand" style="left:294px;top:64px"><span class="brand__name">Tidewell</span></div>
</section>

<!-- Card: Next appointment -->
<section class="card card--appointment">
  <div class="appointment">
    <h2 class="appointment__title">Next Appointment</h2>
    <p class="field" style="left:96px;top:142px">Name:<span class="field__line" style="width:262px"></span></p>
    <p class="field" style="left:96px;top:167px">Date:<span class="field__line" style="width:154px"></span>&nbsp;Time:<span class="field__line" style="width:80px"></span></p>
    <p class="booking">Book Online <span class="booking__link">tidewellcareservices.com.au</span></p>
  </div>
</section>

<!-- Card: Corinne Ashby -->
<section class="card card--corinne">
  <div class="bar bar--accent" style="top:62px;height:56px"></div>
  <div class="bar bar--contact" style="top:150px;height:94px"></div>
  <div class="profile" style="top:58px">
    <h2 class="profile__name">Corinne Ashby</h2>
    <p class="profile__quals">B. Physio</p>
    <p class="profile__quals">Post Grad Certif. Continence &amp; Pelvic Floor Rehabilitation</p>
    <p class="profile__role">Physiotherapist Pelvic Health</p>
  </div>
  <ul class="contacts" style="top:146px">
    <li><svg><use href="#i-pin"/></svg>14 Gallivant Ave, Marrowvale 3188</li>
    <li><svg><use href="#i-phone"/></svg>84316570 Phone</li>
    <li><svg><use href="#i-fax"/></svg>8431 6578 Fax</li>
    <li><svg><use href="#i-mail"/></svg>marla@tidewellcareservices.com.au</li>
    <li><svg><use href="#i-mail"/></svg>info@tidewellcareservices.com.au (office)</li>
    <li><svg style="color:var(--peach)"><use href="#i-web"/></svg>tidewellcareservices.com.au</li>
    <li><svg><use href="#i-social"/></svg>/TidewellOedemaAndFamilyCareClinic</li>
  </ul>
  <div class="brand" style="left:294px;top:64px"><span class="brand__name">Tidewell</span></div>
</section>

<!-- Card: Tessa Rowell -->
<section class="card card--tessa">
  <div class="bar bar--accent" style="top:66px;height:40px"></div>
  <div class="bar bar--contact" style="top:150px;height:94px"></div>
  <div class="profile" style="top:62px">
    <h2 class="profile__name">Tessa Rowell</h2>
    <p class="profile__role">Occupational Therapist</p>
    <p class="profile__role">Lymphoedema Therapist</p>
  </div>
  <ul class="contacts" style="top:146px">
    <li><svg><use href="#i-pin"/></svg>14 Gallivant Ave, Marrowvale 3188</li>
    <li><svg><use href="#i-phone"/></svg>84316570 Phone</li>
    <li><svg><use href="#i-fax"/></svg>8431 6578 Fax</li>
    <li><svg><use href="#i-mail"/></svg>marla@tidewellcareservices.com.au</li>
    <li><svg><use href="#i-mail"/></svg>info@tidewellcareservices.com.au (office)</li>
    <li><svg style="color:var(--peach)"><use href="#i-web"/></svg>tidewellcareservices.com.au</li>
    <li><svg><use href="#i-social"/></svg>/TidewellOedemaAndFamilyCareClinic</li>
  </ul>
  <div class="brand" style="left:296px;top:64px"><span class="brand__name">Tidewell</span></div>
</section>

</body>
</html>
```